Consultancy Business Card Design

We need a business card design for a new company based in singapore called KestrelOak. KestrelOak a boutique consultancy firm offering broad-based business solutions, from conception to re-invention, for ventures from new start-ups to long-running traditional businesses.
Its 2 main divisions (Food & Beverage Operations and Construction & Project Management) have access to a wide range of networks, knowledge bases, and resources to service its clients across numerous diverse sectors. This includes, and is not limited to, construction, F&B, and retail.
We are a company that combines the ambition, boldness and energy of one in the 20s with the dedication, level-headedness and dependability of one entering its 30s. Bridging the experiences of the old with ideals of the young, we draw on the positives of both to create a unique synergy.
We hope to see designs that fits our company profile.
Industry/Entity Type
Boutique
Contact Information for Business Card
KestrelOak(Company Name)
Marcus Thiel (Name)
Principle Consultant (Title)
F&B and Hospitality (Division)
(+65) 8043 5617 (Contact no.)
marcus@kestreloak.com.sg (Email)
Colors
Designer to choose colors to be used in the design.

```html
<!DOCTYPE html>
<html lang="en">
<head>
<meta charset="utf-8">
<title>KestrelOak — Business Card</title>
<link rel="stylesheet" href="https://fonts.googleapis.com/css2?family=Montserrat:wght@300;400;600&display=swap">
<style>
  :root {
    --page-bg: #e6e6e6;
    --card-bg: #2e2e2f;
    --mark-tone: #3b3b3d;
    --accent: #48b2e2;
    --name-light: #8fb6cc;
    --contact: #6a6a6d;
  }
  * { margin: 0; padding: 0; box-sizing: border-box; }
  html, body {
    width: 1200px;
    height: 782px;
    overflow: hidden;
    background: var(--page-bg);
  }
  .card {
    position: absolute;
    left: 100px;
    top: 111px;
    width: 1000px;
    height: 560px;
    background: var(--card-bg);
    font-family: "Montserrat", Arial, sans-serif;
    overflow: hidden;
  }
  .brand-watermark {
    position: absolute;
    left: 420px;
    top: 130px;
    width: 540px;
    text-align: right;
    font-size: 120px;
    font-weight: 600;
    line-height: 1.05;
    letter-spacing: -2px;
    color: var(--mark-tone);
    z-index: 0;
  }
  .identity {
    position: absolute;
    left: 109px;
    top: 122px;
    width: 366px;
    z-index: 1;
  }
  .company {
    font-size: 20px;
    font-weight: 400;
    letter-spacing: 1px;
    color: var(--accent);
    margin-left: 9px;
  }
  .person-name {
    font-size: 39px;
    font-weight: 300;
    letter-spacing: 2px;
    color: var(--name-light);
    line-height: 1.2;
    white-space: nowrap;
  }
  .person-name .surname {
    font-weight: 600;
    color: var(--accent);
  }
  .job-title {
    text-align: right;
    font-size: 16px;
    font-weight: 400;
    letter-spacing: 1px;
    color: var(--accent);
    margin-top: 2px;
  }
  .contact {
    position: absolute;
    left: 75px;
    top: 408px;
    list-style: none;
    font-size: 19px;
    font-weight: 400;
    letter-spacing: 2px;
    line-height: 26px;
    color: var(--contact);
    z-index: 1;
  }
</style>
</head>
<body>
  <main class="card">
    <div class="brand-watermark" aria-hidden="true">Kestrel<br>Oak</div>
    <section class="identity">
      <p class="company">KestrelOak</p>
      <h1 class="person-name">Marcus <span class="surname">Thiel</span></h1>
      <p class="job-title">Principle Consultant</p>
    </section>
    <ul class="contact">
      <li>Division: F&amp;B and Hospitality</li>
      <li>Phone: (+65) 8043 5617</li>
      <li>Email: marcus@kestreloak.com.sg</li>
    </ul>
  </main>
</body>
</html>
```